One business card required with 2 company logos and 2 people's details

One business card required.
No preference on design - One side could show the 2 different business logos for the companies we own. The reverse could have the details shown below.
Another option could be one business one side and one business on the reverse. Happy to receive designs.

Dora Pellham
07700 913 286
Rowena Tindall
07700 958 137

website: quietmeadowbloom.co.uk
email: info@quietmeadowbloom.co.uk

website: brightharbourevents.co.uk
email: info:brightharbourevents.co.uk

May be nice to have icons instead of the words email/website?

I have included different versions of the logos to help with your design.

Contact Information for Business Card

see project overview

Requirements
Must have
• both company logos, both contact names and contact details

```html
<!DOCTYPE html>
<html lang="en">
<head>
<meta charset="utf-8">
<title>Business Card – Bright Harbour Events &amp; Quiet Meadow Bloom</title>
<link rel="stylesheet" href="https://fonts.googleapis.com/css2?family=Roboto:wght@400;500;700&display=swap">
<style>
  :root {
    --backdrop: #1f1f21;
    --card-white: #f7f7f8;
    --deep-blue: #1746c4;
    --bright-blue: #08b4e8;
    --lilac: #8c86d8;
    --name-blue: #1a8fe3;
    --ink: #15151c;
    --navy: #1c2a6e;
  }
  * { box-sizing: border-box; margin: 0; padding: 0; }
  html, body {
    width: 1200px; height: 874px; overflow: hidden;
    background: var(--backdrop);
    font-family: "Roboto", Arial, sans-serif;
  }
  .canvas { position: relative; width: 1200px; height: 874px; }
  .card {
    position: absolute; width: 620px; height: 354px;
    background: var(--card-white); border-radius: 22px; overflow: hidden;
    box-shadow: 0 18px 40px rgba(0,0,0,.45);
  }
  .card--front { left: 500px; top: 56px; }
  .card--back { left: 80px; top: 464px; }

  /* front */
  .brand-pair {
    position: absolute; inset: 0;
    display: flex; align-items: center; justify-content: center; gap: 40px;
  }
  .brand {
    display: flex; align-items: center; gap: 10px;
    font-weight: 500; font-size: 22px; line-height: 1.15; text-align: left;
  }
  .brand--events { color: var(--deep-blue); }
  .brand--bloom { color: var(--navy); }
  .brand__dot { width: 18px; height: 18px; border-radius: 50%; flex: none; }
  .brand--events .brand__dot { background: var(--deep-blue); }
  .brand--bloom .brand__dot { background: var(--lilac); }
  .brand-divider { width: 1px; height: 150px; background: var(--deep-blue); opacity: .6; }

  /* back */
  .back-art { position: absolute; inset: 0; }
  .contact-list {
    position: absolute; left: 40px; top: 30px; list-style: none;
    color: #fff; font-size: 14px; line-height: 21px;
  }
  .contact-list li { display: flex; align-items: center; gap: 10px; }
  .contact-list svg { width: 13px; height: 13px; flex: none; }
  .people {
    position: absolute; right: 46px; bottom: 34px; text-align: right;
  }
  .person__name { color: var(--name-blue); font-weight: 700; font-size: 24px; line-height: 1.1; }
  .person__phone {
    display: flex; justify-content: flex-end; align-items: center; gap: 6px;
    color: var(--ink); font-size: 16px; line-height: 1.3; margin-bottom: 6px;
  }
  .person__phone svg { width: 13px; height: 13px; fill: var(--name-blue); }
</style>
</head>
<body>
<div class="canvas">

  <section class="card card--front" aria-label="Card front with both company names">
    <div class="brand-pair">
      <div class="brand brand--events"><span class="brand__dot"></span><span>Bright Harbour<br>Events</span></div>
      <div class="brand-divider"></div>
      <div class="brand brand--bloom"><span class="brand__dot"></span><span>Quiet Meadow<br>Bloom</span></div>
    </div>
  </section>

  <section class="card card--back" aria-label="Card back with contact details">
    <svg class="back-art" viewBox="0 0 620 354" preserveAspectRatio="none" aria-hidden="true">
      <defs>
        <radialGradient id="bandGlow" cx="0.55" cy="0.45" r="0.6">
          <stop offset="0" stop-color="#0cc4ee"/>
          <stop offset="1" stop-color="#1746c4"/>
        </radialGradient>
      </defs>
      <path d="M0 0 H620 V150 C540 120 430 125 320 170 C210 215 90 235 0 120 Z" fill="url(#bandGlow)"/>
      <path d="M0 128 C90 250 210 228 320 184 C430 140 540 132 620 168" fill="none" stroke="#1746c4" stroke-width="3"/>
      <path d="M0 140 C95 262 215 238 325 194 C435 150 545 145 620 182" fill="none" stroke="#08b4e8" stroke-width="4"/>
      <path d="M10 156 C110 268 225 246 335 204 C445 162 550 158 620 194" fill="none" stroke="#8c86d8" stroke-width="5"/>
    </svg>

    <ul class="contact-list">
      <li><svg viewBox="0 0 16 16"><rect x="1" y="3" width="14" height="10" fill="none" stroke="#fff" stroke-width="1.5"/><path d="M1 3 L8 9 L15 3" fill="none" stroke="#fff" stroke-width="1.5"/></svg>info@quietmeadowbloom.co.uk</li>
      <li><svg viewBox="0 0 16 16"><circle cx="8" cy="8" r="6.5" fill="none" stroke="#fff" stroke-width="1.5"/><path d="M1.5 8 H14.5 M8 1.5 C4 5 4 11 8 14.5 C12 11 12 5 8 1.5" fill="none" stroke="#fff" stroke-width="1.2"/></svg>quietmeadowbloom.co.uk</li>
      <li><svg viewBox="0 0 16 16"><rect x="1" y="3" width="14" height="10" fill="none" stroke="#fff" stroke-width="1.5"/><path d="M1 3 L8 9 L15 3" fill="none" stroke="#fff" stroke-width="1.5"/></svg>info:brightharbourevents.co.uk</li>
      <li><svg viewBox="0 0 16 16"><circle cx="8" cy="8" r="6.5" fill="none" stroke="#fff" stroke-width="1.5"/><path d="M1.5 8 H14.5 M8 1.5 C4 5 4 11 8 14.5 C12 11 12 5 8 1.5" fill="none" stroke="#fff" stroke-width="1.2"/></svg>brightharbourevents.co.uk</li>
    </ul>

    <div class="people">
      <div class="person">
        <div class="person__name">Rowena Tindall</div>
        <div class="person__phone">07700 958 137<svg viewBox="0 0 16 16"><path d="M4 1 L6.5 4.5 L5 6.5 C6 8.5 7.5 10 9.5 11 L11.5 9.5 L15 12 L13 15 C7 14.5 1.5 9 1 3 Z"/></svg></div>
      </div>
      <div class="person">
        <div class="person__name">Dora Pellham</div>
        <div class="person__phone">07700 913 286<svg viewBox="0 0 16 16"><path d="M4 1 L6.5 4.5 L5 6.5 C6 8.5 7.5 10 9.5 11 L11.5 9.5 L15 12 L13 15 C7 14.5 1.5 9 1 3 Z"/></svg></div>
      </div>
    </div>
  </section>

</div>
</body>
</html>
```